Website design for legal tech start up in Switzerland (B2B)

We are for a legal tech start up in Switzerland called KOVA. We have been running since August 2016. This will be our first live website.

We need a website designed and business card design for our start-up in Switzerland. We also need the Web design to be converted into HTML and CSS files.

Function of website:
• To inform potential customers of our services
• Form a key part of our digital marketing and sales footprint.
• Branding

Please find attached logo.
Updates

Project Deadline Extended Reason: Giving us time to review submissions and provide opportunity for more submissions. Added Thursday, February 16, 2017

Project Deadline Extended
Reason: Looking for more idea's not necessarily set on blue and grey colours only.

Target Market(s)

B2B tech powered legal services.

Industry/Entity Type

Legal

Contact Information for Business Card

Lean and slick design.

Coding

Coded - Design and coding required

Number of Pages Required

5+ page

Requirements
Must have
• VERY LEAN AND CLEAN DESIGN!
• We have received many great standard designs, but we are looking for something more out-of-the box: You can get inspiration from these designs: http://www.pixelvane.com/websites/clean/
• Thanks!!
• Easy content management system
• Well structured coding for additional development
• Responsive webpage for all types of devices
• SEO optimized
• Tabs (Home, services, team, careers, blog, contact us)
• Colour scheme complementary to logo
Nice to have
• Look and Design - Approachable, High-tech, Modern
• Easy to add chat bot capability in future
Should not have
• Too busy/ too much clutter
• Not take to long to load

```html
<!DOCTYPE html>
<html lang="en">
<head>
<meta charset="utf-8">
<title>KOVA – Legal</title>
<link rel="stylesheet" href="https://fonts.googleapis.com/css2?family=Raleway:wght@500;600;700;800&family=Open+Sans:ital,wght@0,400;0,600;0,700;1,400&display=swap">
<style>
:root{
  --navy:#1b3a6b;
  --navy-dark:#13294d;
  --ink:#3b3b3b;
  --text:#7a7a7a;
  --line:#e4e4e4;
  --white:#ffffff;
  --dark-band:#111214;
}
*{box-sizing:border-box;margin:0;padding:0}
html,body{width:1200px;height:2368px;overflow:hidden;background:var(--white)}
body{position:relative;font-family:"Open Sans",Arial,sans-serif;color:var(--text)}
.abs{position:absolute}
.heading{font-family:"Raleway",Arial,sans-serif}

/* header */
.top-rule{left:0;top:0;width:1200px;height:4px;background:var(--navy-dark)}
.brand{left:131px;top:26px;font-family:"Raleway",Arial,sans-serif;font-weight:800;font-size:64px;letter-spacing:2px;color:var(--ink);line-height:1}
.header-phone{left:769px;top:28px;display:flex;align-items:center;gap:10px;font-family:"Raleway",sans-serif;font-weight:700;font-size:15px;color:var(--navy)}
.consult-btn{left:908px;top:23px;width:160px;height:35px;border:1.5px solid var(--navy);border-radius:3px;display:flex;align-items:center;justify-content:center;font-family:"Raleway",sans-serif;font-weight:700;font-size:12px;color:var(--navy)}
.main-nav{top:82px;left:0;width:1200px}
.main-nav a{position:absolute;font-family:"Raleway",sans-serif;font-weight:700;font-size:11px;color:var(--ink);text-decoration:none;letter-spacing:.3px}
.main-nav a.active{color:var(--navy)}
.search-icon{left:1052px;top:79px}

/* hero */
.hero{left:0;top:120px;width:1200px;height:516px;background:linear-gradient(180deg,#2e3a78 0%,#5a4c8e 35%,#7a6796 55%,#a48a7e 70%,#3e3f6a 100%)}
.hero-title{left:0;top:246px;width:1200px;text-align:center;font-family:"Raleway",sans-serif;font-weight:800;font-size:58px;color:var(--white);letter-spacing:2px}
.hero-sub{left:280px;top:324px;width:640px;text-align:center;font-family:"Raleway",sans-serif;font-weight:500;font-size:19px;line-height:29px;color:var(--white)}
.hero-dots{left:560px;top:410px;display:flex;gap:16px}
.hero-dots span{width:16px;height:16px;border:2px solid var(--white);border-radius:50%}

/* feature cards */
.card-frame{left:134px;top:564px;width:932px;height:250px;background:var(--white);box-shadow:0 0 0 5px rgba(255,255,255,.5)}
.feature-card{top:584px;width:290px;height:223px;background:linear-gradient(180deg,#bdbdbd 0%,#8a8a8a 45%,#2b2b2b 100%)}
.feature-card h3{position:absolute;left:18px;top:148px;font-family:"Raleway",sans-serif;font-weight:700;font-size:12px;color:var(--white)}
.feature-card p{position:absolute;left:18px;top:170px;width:230px;font-size:11px;line-height:20px;color:var(--white)}

/* welcome */
.section-title{left:0;width:1200px;text-align:center;font-family:"Raleway",sans-serif;font-weight:700;font-size:25px;color:var(--navy)}
.welcome-text{left:170px;width:860px;text-align:center;font-size:11.5px;line-height:22px;color:#8a8a8a}
.ghost-btn{top:1034px;height:33px;border:1.5px solid var(--navy);border-radius:2px;display:flex;align-items:center;justify-content:center;font-family:"Raleway",sans-serif;font-weight:700;font-size:11px;color:var(--navy)}

/* testimonial */
.quote-band{left:0;top:1126px;width:1200px;height:243px;background:linear-gradient(180deg,#222428 0%,#0d0e10 100%)}
.quote-rule{left:178px;top:1203px;width:842px;border-top:1.5px dashed #d8d8d8}
.quote-mark{left:570px;top:1174px;width:58px;height:58px;border-radius:50%;background:var(--white);display:flex;align-items:center;justify-content:center}
.quote-text{left:170px;top:1246px;width:860px;text-align:center;font-style:italic;font-size:13px;line-height:24px;color:#e6e6e6}
.quote-name{left:0;top:1307px;width:1200px;text-align:center;font-family:"Raleway",sans-serif;font-weight:700;font-size:11px;color:var(--white)}

/* services */
.service-box{top:1536px;width:212px;height:210px;border:1px solid var(--line);background:var(--white);text-align:center}
.service-icon{position:absolute;left:62px;top:-44px;width:88px;height:88px;border-radius:50%;background:var(--white);border:1px solid #eee;display:flex;align-items:center;justify-content:center}
.service-box h4{position:absolute;left:0;top:62px;width:100%;font-family:"Raleway",sans-serif;font-weight:700;font-size:13px;color:var(--navy)}
.service-box .bar{position:absolute;left:76px;top:86px;width:60px;height:2px;background:var(--navy)}
.service-box p{position:absolute;left:20px;top:100px;width:172px;font-size:11px;line-height:21px;color:#8a8a8a}
.service-box a{position:absolute;left:0;top:172px;width:100%;font-style:italic;font-size:11px;color:var(--navy);text-decoration:none}

/* blog */
.blog-photo{left:0;top:1811px;width:600px;height:329px;background:linear-gradient(120deg,#cfd8e2 0%,#9fb0c3 40%,#2d3d5c 80%,#e8ebee 100%)}
.blog-panel{left:600px;top:1811px;width:600px;height:329px;background:var(--navy)}
.blog-label{left:660px;top:1868px;font-family:"Raleway",sans-serif;font-weight:700;font-size:17px;color:var(--white)}
.blog-arrows{left:1024px;top:1869px;display:flex;gap:6px}
.blog-arrows span{width:19px;height:18px;border:1px solid var(--white);display:flex;align-items:center;justify-content:center}
.blog-title{left:660px;top:1905px;font-family:"Raleway",sans-serif;font-weight:700;font-size:13px;color:var(--white)}
.blog-text{left:660px;top:1934px;width:410px;font-size:11px;line-height:21px;color:#e3e8f0}
.posted-btn{left:660px;top:2045px;width:144px;height:32px;border:1.5px solid var(--white);display:flex;align-items:center;justify-content:center;font-family:"Raleway",sans-serif;font-weight:700;font-size:10.5px;color:var(--white)}

/* footer */
.footer-brand{left:133px;top:2176px;font-family:"Raleway",sans-serif;font-weight:800;font-size:56px;letter-spacing:2px;color:var(--ink);line-height:1}
.copyright{left:133px;top:2248px;width:177px;text-align:center;font-size:9px;color:var(--ink)}
.social{left:166px;top:2276px;display:flex;gap:4px}
.social span{width:23px;height:23px;border-radius:50%;border:1.5px solid var(--navy)}
.footer-heading{top:2186px;font-family:"Raleway",sans-serif;font-weight:700;font-size:12px;color:var(--ink)}
.contact-item{left:377px;display:flex;gap:12px;font-size:12px;line-height:19px;color:#6a6a6a}
.contact-item svg{flex:none;margin-top:2px}
.field{left:666px;width:247px;height:38px;border:1px solid var(--line);font-size:10px;color:#555;padding:12px 12px}
.subscribe{left:821px;top:2274px;width:92px;height:38px;background:var(--navy);color:var(--white);font-family:"Raleway",sans-serif;font-weight:700;font-size:10.5px;display:flex;align-items:center;justify-content:center}
.quick-links{left:992px;top:2214px;list-style:none}
.quick-links li{font-size:11px;line-height:18.6px;color:#555;padding-left:16px;position:relative}
.quick-links li::before{content:"";position:absolute;left:2px;top:6px;border-left:5px solid #555;border-top:3.5px solid transparent;border-bottom:3.5px solid transparent}
</style>
</head>
<body>

<header>
  <div class="abs top-rule"></div>
  <div class="abs brand">KOVA</div>
  <div class="abs header-phone">
    <svg width="18" height="18" viewBox="0 0 24 24" fill="none" stroke="#1b3a6b" stroke-width="2"><path d="M5 3h4l2 5-3 2a12 12 0 0 0 6 6l2-3 5 2v4a2 2 0 0 1-2 2A17 17 0 0 1 3 5a2 2 0 0 1 2-2z"/></svg>
    (345) 555-0142
  </div>
  <div class="abs consult-btn">MAKE AN CONSULTATION</div>
  <nav class="abs main-nav">
    <a class="active" style="left:534px">HOME</a>
    <a style="left:612px">SERVICES</a>
    <a style="left:707px">TEAM</a>
    <a style="left:783px">CAREERS</a>
    <a style="left:878px">BLOG</a>
    <a style="left:953px">CONTACT US</a>
  </nav>
  <svg class="abs search-icon" width="18" height="18" viewBox="0 0 24 24" fill="none" stroke="#3b3b3b" stroke-width="2"><circle cx="10" cy="10" r="7"/><path d="M15 15l6 6"/></svg>
</header>

<section>
  <div class="abs hero" role="img" aria-label="Evening view of a Swiss old town along a river with church spires and city lights"></div>
  <h1 class="abs hero-title">KOVA LEGAL</h1>
  <p class="abs hero-sub">Similique sunt in culpa qui officia deserunt mollitia animi, id est laborum dolorum fuga. Et harum quidem rerum facilis est...</p>
  <div class="abs hero-dots"><span></span><span></span><span></span></div>
</section>

<section>
  <div class="abs card-frame"></div>
  <div class="abs feature-card" style="left:152px" role="img" aria-label="Lawyer in a suit at a desk">
    <h3>DESERUNT MOLLITIA</h3><p>Pursues or desires to obtain pain of itself, it is pain, but because...</p>
  </div>
  <div class="abs feature-card" style="left:455px" role="img" aria-label="Team of lawyers standing together in an office">
    <h3>DESERUNT MOLLITIA</h3><p>Pursues or desires to obtain pain of itself, it is pain, but because...</p>
  </div>
  <div class="abs feature-card" style="left:760px" role="img" aria-label="Hand stamping a legal document">
    <h3>DESERUNT MOLLITIA</h3><p>Pursues or desires to obtain pain of itself, it is pain, but because...</p>
  </div>
</section>

<section>
  <h2 class="abs section-title" style="top:848px">WELCOME TO KOVA</h2>
  <p class="abs welcome-text" style="top:892px">Similique sunt in culpa qui officia deserunt mollitia animi, id est laborum et dolorum fuga. Et harum quidem rerum facilis est et expedita distinctio. Nam libero tempore, cum soluta nobis est eligendi optio cumque nihil impedit quo minus id quod maxime placeat facere possimusomnis voluptas assumenda est, omnis dolor repellendus. Temporibus autem quibusdam et aut officiis debitis...</p>
  <p class="abs welcome-text" style="top:968px">Placeat facere possimus, omnis voluptas assumenda est, omnis dolor repellendus. Temporibus autem quibusdam et aut officiis debitis aut rerum necessitatibus saepe eveniet ut et voluptates repudiandae sint et molestiae non recusandae. Itaque earum rerum hic tenetur a sapiente...</p>
  <div class="abs ghost-btn" style="left:478px;width:119px">LEARN MORE INFO</div>
  <div class="abs ghost-btn" style="left:603px;width:120px">GET START TODAY</div>
</section>

<section>
  <div class="abs quote-band" role="img" aria-label="Darkened photo of a group of business people"></div>
  <div class="abs quote-rule"></div>
  <div class="abs quote-mark">
    <svg width="22" height="18" viewBox="0 0 22 18" fill="#1b3a6b"><circle cx="5" cy="6" r="5"/><path d="M9 6c0 6-3 10-7 11l-1-2c3-1 4-4 4-7z"/><circle cx="16" cy="6" r="5"/><path d="M20 6c0 6-3 10-7 11l-1-2c3-1 4-4 4-7z"/></svg>
  </div>
  <svg class="abs" style="left:114px;top:1214px" width="16" height="64" viewBox="0 0 16 64" fill="none" stroke="#cfcfcf" stroke-width="1.5"><path d="M14 1L2 32l12 31"/></svg>
  <svg class="abs" style="left:1070px;top:1214px" width="16" height="64" viewBox="0 0 16 64" fill="none" stroke="#cfcfcf" stroke-width="1.5"><path d="M2 1l12 31L2 63"/></svg>
  <p class="abs quote-text">Nam libero tempore, cum soluta nobis est eligendi optio cumque nihil impedit quo minus id quod maxime placeat facere possimus, omnis voluptas assumenda est, omnis dolor repellendus. Temporibus autem quibusdam et aut officiis debitis aut rerum...</p>
  <div class="abs quote-name">-MARA VOSS</div>
</section>

<section>
  <h2 class="abs section-title" style="top:1422px">OUR SERVICES</h2>

  <div class="abs service-box" style="left:133px">
    <div class="service-icon"><svg width="34" height="38" viewBox="0 0 34 38" fill="none" stroke="#1b3a6b" stroke-width="1.6"><path d="M4 1h18l8 8v28H4z"/><path d="M22 1v8h8M9 15h16M9 20h16M9 25h16M9 30h10"/></svg></div>
    <h4>CUM SOLUTA</h4><div class="bar"></div>
    <p>Omnis voluptas assumenda omnis dolor repellendus. Temporibus autem quibusdam...</p>
    <a>Learn More Information!</a>
  </div>
  <div class="abs service-box" style="left:373px">
    <div class="service-icon"><svg width="38" height="38" viewBox="0 0 38 38" fill="none" stroke="#1b3a6b" stroke-width="1.6"><circle cx="15" cy="15" r="8"/><circle cx="15" cy="15" r="3"/><path d="M15 3v4M15 23v4M3 15h4M23 15h4M6.5 6.5l3 3M20.5 20.5l3 3M6.5 23.5l3-3M20.5 9.5l3-3"/><circle cx="28" cy="28" r="5"/><circle cx="28" cy="28" r="1.8"/></svg></div>
    <h4>REPUDIANDAE SINT</h4><div class="bar"></div>
    <p>Omnis voluptas assumenda omnis dolor repellendus. Temporibus autem quibusdam...</p>
    <a>Learn More Information!</a>
  </div>
  <div class="abs service-box" style="left:614px">
    <div class="service-icon"><svg width="40" height="34" viewBox="0 0 40 34" fill="none" stroke="#1b3a6b" stroke-width="1.6"><path d="M2 12l8-8 8 4 6-3 14 9-10 12-6-4M2 12l12 14 4-2 4 3 4-2"/><path d="M18 8l-6 6 3 2 6-5"/></svg></div>
    <h4>SIMILIQUE SUNT</h4><div class="bar"></div>
    <p>Omnis voluptas assumenda omnis dolor repellendus. Temporibus autem quibusdam...</p>
    <a>Learn More Information!</a>
  </div>
  <div class="abs service-box" style="left:854px">
    <div class="service-icon"><svg width="40" height="34" viewBox="0 0 40 34" fill="none" stroke="#1b3a6b" stroke-width="1.6"><circle cx="20" cy="9" r="6"/><circle cx="8" cy="13" r="4.5"/><circle cx="32" cy="13" r="4.5"/><path d="M10 32v-6a10 10 0 0 1 20 0v6zM1 30v-3a7 7 0 0 1 10-6M39 30v-3a7 7 0 0 0-10-6"/></svg></div>
    <h4>ASSUMENDA</h4><div class="bar"></div>
    <p>Omnis voluptas assumenda omnis dolor repellendus. Temporibus autem quibusdam...</p>
    <a>Learn More Information!</a>
  </div>
</section>

<section>
  <div class="abs blog-photo" role="img" aria-label="Two businessmen smiling while reviewing a tablet"></div>
  <div class="abs blog-panel"></div>
  <div class="abs blog-label">RECENT BLOG</div>
  <div class="abs blog-arrows">
    <span><svg width="8" height="10" viewBox="0 0 8 10" fill="none" stroke="#fff" stroke-width="1.5"><path d="M6 1L2 5l4 4"/></svg></span>
    <span><svg width="8" height="10" viewBox="0 0 8 10" fill="none" stroke="#fff" stroke-width="1.5"><path d="M2 1l4 4-4 4"/></svg></span>
  </div>
  <div class="abs blog-title">Nam libero tempore, cum soluta nobis est eligendi optio</div>
  <p class="abs blog-text">Ducimus qui blanditiis praesentium voluptatum deleniti atque corrupti quos dolores et quas molestias excepturi sint occaecati cupiditate non provident, similique sunt in culpa qui officia deserunt mollitia animi, id est laborum et dolorum fuga. Et harum quidem rerum facilis est et expedita distinctio...</p>
  <div class="abs posted-btn">POSTED ON 23 JAN 2017</div>
</section>

<footer>
  <div class="abs footer-brand">KOVA</div>
  <div class="abs copyright">COPYRIGHTS © 2017 KOVA.</div>
  <div class="abs social" aria-label="Social links"><span></span><span></span><span></span><span></span></div>

  <div class="abs footer-heading" style="left:377px">CONTACT US</div>
  <div class="abs contact-item" style="top:2218px">
    <svg width="12" height="15" viewBox="0 0 12 15" fill="#8a8a8a"><path d="M6 0a6 6 0 0 0-6 6c0 4 6 9 6 9s6-5 6-9a6 6 0 0 0-6-6zm0 8.5A2.5 2.5 0 1 1 6 3.5a2.5 2.5 0 0 1 0 5z"/></svg>
    <span>224#KOVA Company Name P.O. Box<br>Strett name,City-5345</span>
  </div>
  <div class="abs contact-item" style="top:2272px">
    <svg width="13" height="13" viewBox="0 0 24 24" fill="#8a8a8a"><path d="M5 2h4l2 5-3 2a12 12 0 0 0 6 6l2-3 5 2v4a2 2 0 0 1-2 2A18 18 0 0 1 3 4a2 2 0 0 1 2-2z"/></svg>
    <span>Phone: (345) 555-0142</span>
  </div>
  <div class="abs contact-item" style="top:2308px">
    <svg width="13" height="11" viewBox="0 0 13 11" fill="#8a8a8a"><path d="M0 0h13v11H0zm1 1.5V10h11V1.5L6.5 6z"/></svg>
    <span>Email: KOVA.COM</span>
  </div>

  <div class="abs footer-heading" style="left:666px">SIGNUP FOR NEWSLETTER</div>
  <div class="abs field" style="top:2225px">Enter Name</div>
  <div class="abs field" style="top:2274px">Enter Email</div>
  <div class="abs subscribe">SUBSCRIBE</div>

  <div class="abs footer-heading" style="left:992px">QUICK LINKS</div>
  <ul class="abs quick-links">
    <li>Home</li><li>Services</li><li>Team</li><li>Careers</li><li>Blog</li><li>Contact us</li>
  </ul>
</footer>

</body>
</html>
```